Gardening and life coaching business card design

I need business cards for a new company in the heart of the Ozarks at the Lake of the Ozarks. Maple Hollow Unlimited's mission is to teach the world to fish. We provide fresh local fish and produce using permaculture methods. We work with nature and the flow to create more harmony and less impact. We also coach others who are ready to make this transition. We specialize in microgreens and Aquaculture systems. I would like to make Maple Hollow Unlimited come alive with green vines and purple flowers I wold like Maple Hollow Unlimited to be in green and the rest of the lettering to be in purple. The feel of the card should be that of the Garden of Eden.

Life Coaching

Maple Hollow Unlimited
Owner/Operator Dorothea Fenwick
Contact Info:
(555) 214-0683
maplehollowunlimited.com
maplehollowunlimited is also on FB

```html
<!DOCTYPE html>
<html lang="en">
<head>
<meta charset="utf-8">
<title>Maple Hollow Unlimited – Business Card</title>
<link href="https://fonts.googleapis.com/css2?family=Tinos:wght@400;700&display=swap" rel="stylesheet">
<style>
  :root {
    --backdrop: #e9e6e1;
    --card-white: #ffffff;
    --leaf-green: #6cbf45;
    --leaf-pale: #dfe6dc;
    --leaf-deep: #3f8f2a;
    --ink-black: #111111;
    --text-dark: #1c1c1c;
    --text-light: #ffffff;
  }
  * { margin: 0; padding: 0; box-sizing: border-box; }
  html, body {
    width: 1200px;
    height: 848px;
    overflow: hidden;
    background: var(--backdrop);
    font-family: "Tinos", "Times New Roman", serif;
  }
  .sheet {
    width: 1200px;
    height: 848px;
    display: flex;
    flex-direction: column;
    align-items: center;
    justify-content: center;
    gap: 32px;
  }
  .card {
    width: 660px;
    height: 377px;
    position: relative;
    overflow: hidden;
    box-shadow: 0 4px 14px rgba(0,0,0,0.18);
  }

  /* Front side */
  .card-front {
    background: var(--card-white);
    border-top: 9px solid var(--ink-black);
  }
  .card-front .bottom-band {
    position: absolute;
    left: 0; right: 0; bottom: 0;
    height: 20px;
    background: var(--leaf-green);
  }
  .brand-front {
    position: absolute;
    top: 38px;
    left: 150px;
    display: flex;
    align-items: center;
    gap: 14px;
  }
  .brand-front .company-name {
    font-weight: 700;
    font-size: 30px;
    letter-spacing: 1px;
    text-transform: uppercase;
    color: var(--ink-black);
    white-space: nowrap;
  }
  .brand-front .brand-dot {
    width: 96px;
    height: 96px;
    border-radius: 50%;
    background: var(--leaf-pale);
    flex: none;
  }
  .card-front .person {
    position: absolute;
    top: 150px;
    left: 190px;
    width: 260px;
    text-align: center;
    color: var(--text-dark);
  }
  .person .person-name {
    font-size: 27px;
    line-height: 1.1;
  }
  .person .person-role {
    font-size: 16px;
    margin-top: 2px;
  }
  .card-front .contact {
    position: absolute;
    top: 255px;
    left: 240px;
    width: 320px;
    text-align: center;
    list-style: none;
    font-size: 21px;
    line-height: 1.2;
    color: var(--text-dark);
  }

  /* Back side */
  .card-back {
    background: var(--leaf-green);
    border-right: 12px solid var(--ink-black);
  }
  .brand-back {
    position: absolute;
    top: 150px;
    left: 0; right: 0;
    display: flex;
    align-items: center;
    justify-content: center;
    gap: 16px;
  }
  .brand-back .company-name {
    font-weight: 700;
    font-size: 32px;
    letter-spacing: 2px;
    text-transform: uppercase;
    color: var(--text-light);
    white-space: nowrap;
  }
  .brand-back .brand-dot {
    width: 62px;
    height: 62px;
    border-radius: 50%;
    background: var(--leaf-deep);
    flex: none;
  }
</style>
</head>
<body>
  <main class="sheet">
    <section class="card card-front" aria-label="Card front">
      <div class="brand-front">
        <h1 class="company-name">Maple Hollow Unlimited</h1>
        <span class="brand-dot" aria-hidden="true"></span>
      </div>
      <div class="person">
        <p class="person-name">Dorothea Fenwick</p>
        <p class="person-role">Owner/Operator</p>
      </div>
      <ul class="contact">
        <li>P: (555) 214-0683</li>
        <li>w: maplehollowunlimited.com</li>
        <li>f: maplehollowunlimited</li>
      </ul>
      <div class="bottom-band"></div>
    </section>

    <section class="card card-back" aria-label="Card back">
      <div class="brand-back">
        <p class="company-name">Maple Hollow Unlimited</p>
        <span class="brand-dot" aria-hidden="true"></span>
      </div>
    </section>
  </main>
</body>
</html>
```